Verdant Systems Business Card

want the back of card to be blue- with the logo in the center
front of card- info plus logo (info being mailing address, email address, and website address )
4 different names with titles to have on cards
1) Calvin Borsted - Owner
2) Naomi Trelvik- Customer Relationship Specialist
3) Felix Andrade- Vice President of Sales
4) Owen Markby- Chief Technology Officer

Target Market(s)

tech company in the government/probation office industry

Industry/Entity Type

Government Office

Contact Information for Business Card

1) Calvin Borsted - Owner

Colors
0355a3
ffffff

Requirements
Must have
• back side should be blue, with the logo placed in the center
• front side needs to include both the logo, as well as company info (info should include website address, email address, and mailing address)

```html
<!DOCTYPE html>
<html lang="en">
<head>
<meta charset="utf-8">
<title>Verdant Systems Business Card</title>
<link rel="stylesheet" href="https://fonts.googleapis.com/css2?family=PT+Serif:wght@400;700&family=Roboto:wght@400&display=swap">
<style>
  :root {
    --backdrop: #e4e4e6;
    --card: #ffffff;
    --navy: #27386c;
    --navy-deep: #1b2852;
    --slate: #8b8b96;
    --text-grey: #6f7079;
    --faint: #f0f0f2;
    --on-navy: #ffffff;
  }
  * { margin: 0; padding: 0; box-sizing: border-box; }
  html, body { width: 1200px; height: 1200px; overflow: hidden; }
  body { background: var(--backdrop); position: relative; font-family: "Roboto", Arial, sans-serif; }

  .card {
    position: absolute;
    border-radius: 20px;
    overflow: hidden;
  }
  .card--logo { left: 238px; top: 120px; width: 712px; height: 417px; background: var(--navy); }
  .card--contact { left: 231px; top: 645px; width: 711px; height: 416px; background: var(--card); }

  .brand { position: absolute; display: flex; flex-direction: column; align-items: center; }
  .brand__dot { border-radius: 50%; background: var(--navy); }
  .brand__name {
    font-family: "PT Serif", Georgia, serif;
    font-weight: 700;
    color: var(--navy);
    white-space: nowrap;
    text-transform: uppercase;
  }

  .card--logo .brand { left: 0; right: 0; top: 100px; }
  .card--logo .brand__dot { width: 70px; height: 70px; margin-bottom: 30px; background: var(--on-navy); }
  .card--logo .brand__name { font-size: 52px; letter-spacing: 2px; color: var(--on-navy); }

  .web-line {
    position: absolute; left: 0; right: 0; top: 374px;
    display: flex; justify-content: center; align-items: center; gap: 22px;
    font-size: 17px; color: var(--on-navy);
  }
  .web-line__rule { width: 48px; height: 3px; background: var(--on-navy); border-radius: 2px; }

  .footer-band { position: absolute; left: 0; right: 0; bottom: 0; height: 14px; display: flex; }
  .footer-band__navy { width: 357px; background: var(--navy-deep); }
  .footer-band__grey { flex: 1; background: var(--slate); }

  .faint-mark {
    position: absolute; left: 410px; top: 30px; width: 290px; height: 290px;
    border-radius: 50%; background: var(--faint);
  }

  .person { position: absolute; left: 37px; top: 44px; }
  .person__name { font-family: "PT Serif", Georgia, serif; font-weight: 400; font-size: 26px; color: var(--navy); text-transform: uppercase; }
  .person__title { font-size: 17px; color: var(--text-grey); margin-top: 4px; }

  .contact { position: absolute; left: 37px; top: 244px; font-size: 17.5px; color: var(--text-grey); }
  .contact__address { line-height: 29px; margin-bottom: 4px; }
  .contact__row { display: flex; align-items: center; gap: 13px; height: 26px; }
  .contact__icon { width: 18px; height: 18px; flex: none; }

  .card--contact .brand { left: 405px; width: 270px; top: 226px; }
  .card--contact .brand__dot { width: 42px; height: 42px; margin-bottom: 24px; }
  .card--contact .brand__name { font-size: 26px; letter-spacing: 1px; }
</style>
</head>
<body>
  <section class="card card--logo">
    <div class="brand">
      <span class="brand__dot"></span>
      <span class="brand__name">Verdant Systems</span>
    </div>
    <div class="web-line">
      <span class="web-line__rule"></span>
      <span>www.verdantsystems.com</span>
      <span class="web-line__rule"></span>
    </div>
    <div class="footer-band"><span class="footer-band__navy"></span><span class="footer-band__grey"></span></div>
  </section>

  <section class="card card--contact">
    <span class="faint-mark"></span>
    <div class="person">
      <h1 class="person__name">Naomi Trelvik</h1>
      <p class="person__title">Customer Relationship Specialist</p>
    </div>
    <div class="contact">
      <p class="contact__address">234 Anywhere St., Any City,<br>Any Town, US 123456</p>
      <p class="contact__row">
        <svg class="contact__icon" viewBox="0 0 20 20"><path fill="#27386c" d="M3 7c0-3 3-4 7-4s7 1 7 4v1h-4V6H7v2H3zM5 9h10l2 8H3z"/></svg>
        111-111-1111
      </p>
      <p class="contact__row">
        <svg class="contact__icon" viewBox="0 0 20 20"><rect x="2" y="4" width="16" height="12" fill="#27386c"/><path d="M2 4l8 7 8-7" fill="none" stroke="#fff" stroke-width="1.5"/></svg>
        naomi.t@verdantsystems.com
      </p>
      <p class="contact__row">
        <svg class="contact__icon" viewBox="0 0 20 20"><circle cx="10" cy="10" r="7.5" fill="#27386c"/><path d="M2.5 10h15M10 2.5c-3 3-3 12 0 15M10 2.5c3 3 3 12 0 15" fill="none" stroke="#fff" stroke-width="1"/></svg>
        www.verdantsystems.com
      </p>
    </div>
    <div class="brand">
      <span class="brand__dot"></span>
      <span class="brand__name">Verdant Systems</span>
    </div>
  </section>
</body>
</html>
```